Realtor branding business card

modern, simple and self branding. Broker office logo needs to be used but not emphasized. Looking to brand myself

Target Market(s)

buyers, sellers and investors

Industry/Entity Type

Realtor

Contact Information for Business Card

Sample of my current business card on file

Requirements
Must have
• my website - tobiasmerrowkl.com
• Realtor logo
• Fair housing logo
Nice to have
• Colors from office logo but not a must
Should not have
• Do not want headshot

```html
<!DOCTYPE html>
<html lang="en">
<head>
<meta charset="utf-8">
<title>Tobias Merrow, PA – Business Card</title>
<link rel="stylesheet" href="https://fonts.googleapis.com/css2?family=Libre+Baskerville:wght@700&family=Nunito+Sans:wght@400;600;900&display=swap">
<style>
  :root {
    --backdrop: #e9e7e3;
    --paper: #ffffff;
    --paper-shade: #f1f1f1;
    --ink: #333333;
    --ink-soft: #555555;
    --brand-blue: #1d4fa3;
    --navy-light: #1f5684;
    --navy-dark: #0c2d4f;
    --rule: #c9c9c9;
    --badge: #4a4a4a;
  }
  * { box-sizing: border-box; margin: 0; padding: 0; }
  html, body { width: 1200px; height: 900px; overflow: hidden; }
  body {
    background: var(--backdrop);
    display: flex;
    flex-direction: column;
    align-items: center;
    justify-content: center;
    gap: 34px;
    font-family: "Nunito Sans", sans-serif;
  }
  .card {
    width: 700px;
    height: 400px;
    position: relative;
    box-shadow: 0 10px 28px rgba(0,0,0,0.18);
    overflow: hidden;
  }

  /* Front */
  .card-front {
    background: linear-gradient(180deg, var(--paper-shade) 0%, var(--paper) 45%);
  }
  .identity {
    position: absolute;
    left: 0;
    width: 300px;
    top: 112px;
    text-align: right;
  }
  .agent-name {
    font-family: "Libre Baskerville", serif;
    font-weight: 700;
    font-size: 25px;
    color: var(--ink);
    letter-spacing: 0.2px;
  }
  .agent-title {
    font-size: 19px;
    font-weight: 400;
    color: var(--brand-blue);
    letter-spacing: 1px;
    margin-top: 2px;
  }
  .divider {
    position: absolute;
    left: 322px;
    top: 70px;
    width: 2px;
    height: 102px;
    background: var(--rule);
  }
  .contact-list {
    position: absolute;
    left: 346px;
    top: 70px;
    list-style: none;
  }
  .contact-list li {
    display: flex;
    align-items: center;
    font-size: 16px;
    color: var(--ink-soft);
    line-height: 20px;
    letter-spacing: 0.4px;
  }
  .contact-list .icon {
    width: 15px;
    height: 15px;
    margin-right: 12px;
    flex: none;
  }
  .contact-list .no-icon { padding-left: 27px; }

  .social {
    position: absolute;
    right: 46px;
    top: 222px;
    display: flex;
    align-items: center;
    gap: 10px;
    font-size: 16px;
    color: var(--ink-soft);
    letter-spacing: 0.4px;
  }
  .social .dot {
    width: 15px; height: 15px; border-radius: 50%;
    background: var(--brand-blue);
  }

  .brokerage {
    position: absolute;
    left: 60px;
    bottom: 46px;
    font-weight: 900;
    font-size: 30px;
    line-height: 1;
    color: var(--brand-blue);
    letter-spacing: -0.3px;
  }
  .badges {
    position: absolute;
    left: 330px;
    bottom: 62px;
    display: flex;
    gap: 10px;
  }
  .badge {
    width: 30px; height: 26px;
    background: var(--badge);
    border-radius: 2px;
  }

  /* Back */
  .card-back {
    background: radial-gradient(ellipse at 45% 40%, var(--navy-light) 0%, var(--navy-dark) 80%);
    color: var(--paper);
  }
  .back-brand {
    position: absolute;
    left: 0; right: 0;
    top: 120px;
    text-align: center;
    font-weight: 900;
    font-size: 60px;
    line-height: 1.05;
    color: var(--paper);
    letter-spacing: -0.5px;
  }
  .back-site {
    position: absolute;
    left: 0; right: 0;
    bottom: 80px;
    text-align: center;
    font-size: 18px;
    letter-spacing: 1px;
    color: var(--paper);
  }
</style>
</head>
<body>

  <section class="card card-front">
    <div class="identity">
      <div class="agent-name">Tobias Merrow, PA</div>
      <div class="agent-title">REALTOR</div>
    </div>
    <div class="divider"></div>
    <ul class="contact-list">
      <li>
        <svg class="icon" viewBox="0 0 16 16" aria-hidden="true"><circle cx="8" cy="8" r="8" fill="var(--brand-blue)"/><path d="M5 4.5 L6.6 4.3 L7.2 6.2 L6.3 7 Q7 8.6 8.9 9.6 L9.7 8.8 L11.6 9.4 L11.4 11 Q7.6 11.4 5 8 Q4.4 6 5 4.5 Z" fill="#fff"/></svg>
        Cell : 407 555 0147
      </li>
      <li>
        <svg class="icon" viewBox="0 0 16 16" aria-hidden="true"><circle cx="8" cy="8" r="8" fill="var(--brand-blue)"/><rect x="4" y="6.5" width="8" height="4.5" rx="1" fill="#fff"/><path d="M4 6.5 Q8 3.5 12 6.5" stroke="#fff" stroke-width="1.3" fill="none"/></svg>
        Office : 407 555 0182
      </li>
      <li>
        <svg class="icon" viewBox="0 0 16 16" aria-hidden="true"><circle cx="8" cy="8" r="8" fill="var(--brand-blue)"/><rect x="4" y="5" width="8" height="6" fill="#fff"/><path d="M4 5 L8 8.4 L12 5" stroke="var(--brand-blue)" stroke-width="1" fill="none"/></svg>
        merrowrealty@mail.com
      </li>
      <li>
        <svg class="icon" viewBox="0 0 16 16" aria-hidden="true"><circle cx="8" cy="8" r="8" fill="var(--brand-blue)"/><path d="M8 12.5 L5.4 8 A3 3 0 1 1 10.6 8 Z" fill="#fff"/><circle cx="8" cy="6.6" r="1.1" fill="var(--brand-blue)"/></svg>
        48 Linden Crest Drive.
      </li>
      <li class="no-icon">Maplewood Springs. FL 32799</li>
    </ul>

    <div class="social">
      <span class="dot"></span>
      <span>@tobiasmerrowpa</span>
    </div>

    <div class="brokerage">Brightdoor<br>Realty Group</div>
    <div class="badges">
      <span class="badge" role="img" aria-label="Fair housing badge"></span>
      <span class="badge" role="img" aria-label="Realtor badge"></span>
    </div>
  </section>

  <section class="card card-back">
    <div class="back-brand">Brightdoor<br>Realty Group</div>
    <div class="back-site">www.tobiasmerrowkl.com</div>
  </section>

</body>
</html>
```